QVR business card

Need a business card for a company that provides instructional design and elearning development services. The website is here: http://quorvane.studio/

I'm attaching a current logo, as well as the old business card design. While I like to keep it clean, the old design is too simplistic for my liking. The only idea I want to reuse from the old design is placing industry jargon on the back of the card, just need a better way to present it. But if you have other ideas for the back--feel free to experiment.

Please use the colors complementary to the color we have on the website. Thank you!

```html
<!DOCTYPE html>
<html lang="en">
<head>
<meta charset="utf-8">
<title>QVR Business Card</title>
<link href="https://fonts.googleapis.com/css2?family=Open+Sans:wght@400;600;700&display=swap" rel="stylesheet">
<style>
  :root {
    --teal: #14b1b1;
    --teal-deep: #0fa3a6;
    --sand: #e4d49b;
    --gold: #d8c48a;
    --gold-text: #d6c07c;
    --ink: #2b2b2b;
    --white: #ffffff;
    --stage: #2b2b2b;
  }
  * { box-sizing: border-box; margin: 0; padding: 0; }
  html, body { width: 1200px; height: 900px; overflow: hidden; }
  body {
    background: var(--stage);
    font-family: "Open Sans", Arial, sans-serif;
    position: relative;
  }
  .card {
    position: absolute;
    width: 560px;
    height: 320px;
    border-radius: 3px;
    overflow: hidden;
    box-shadow: 0 12px 28px rgba(0,0,0,.45);
  }

  /* Back of card */
  .card-back {
    left: 70px; top: 90px;
    background: linear-gradient(180deg, var(--teal) 0%, #8fc6a8 55%, var(--sand) 100%);
    color: var(--white);
  }
  .world-map {
    position: absolute;
    left: 150px; top: 75px;
    width: 300px; height: 170px;
    border-radius: 40px;
    background: radial-gradient(ellipse at center, rgba(20,150,150,.35), rgba(20,150,150,0) 70%);
  }
  .brand-mark {
    position: absolute;
    left: 0; right: 0; top: 70px;
    display: flex; justify-content: center; align-items: center; gap: 10px;
    font-weight: 700; font-size: 34px; letter-spacing: 2px;
  }
  .brand-mark .dot {
    width: 18px; height: 18px; border-radius: 50%; background: var(--white);
  }
  .services {
    position: absolute;
    left: 0; right: 0; top: 132px;
    display: flex; flex-direction: column; align-items: center; gap: 4px;
  }
  .service-tag {
    background: var(--teal-deep);
    color: var(--white);
    font-size: 15px;
    line-height: 20px;
    padding: 0 8px;
    border-radius: 3px;
  }
  .back-url {
    position: absolute; left: 0; right: 0; top: 240px;
    text-align: center; font-size: 12px;
  }

  /* Front of card */
  .card-front {
    left: 570px; top: 490px;
    background: var(--white);
  }
  .card-front svg { position: absolute; inset: 0; }
  .front-brand {
    position: absolute; left: 62px; top: 178px;
    display: flex; align-items: center; gap: 10px;
    color: var(--teal);
    font-weight: 700; font-size: 40px; letter-spacing: 1px;
  }
  .front-brand .dot {
    width: 22px; height: 22px; border-radius: 50%; background: var(--teal);
  }
  .holder {
    position: absolute; left: 318px; top: 70px;
  }
  .holder-name {
    color: var(--gold-text); font-weight: 700; font-size: 17px; letter-spacing: .3px;
  }
  .holder-role { color: var(--ink); font-size: 13px; margin-top: 1px; }
  .contacts {
    position: absolute; left: 385px; top: 198px;
    list-style: none; color: var(--white); font-size: 12.5px;
  }
  .contacts li { display: flex; align-items: center; gap: 8px; height: 20px; }
  .contacts svg { position: static; width: 12px; height: 12px; flex: none; }
</style>
</head>
<body>

<section class="card card-back" aria-label="Card back">
  <div class="world-map" role="img" aria-label="Dotted world map"></div>
  <div class="brand-mark"><span class="dot"></span><span>QVR</span></div>
  <div class="services">
    <span class="service-tag">Instructional Design</span>
    <span class="service-tag">Elearning Development | Mobile Learning</span>
    <span class="service-tag">Instructor-LED Training</span>
  </div>
  <p class="back-url">www.quorvane.studio</p>
</section>

<section class="card card-front" aria-label="Card front">
  <svg viewBox="0 0 560 320" width="560" height="320" aria-hidden="true">
    <path d="M222 0 H560 V108 L352 158 Q318 166 300 146 Q262 100 236 30 Q230 12 222 0 Z"
          fill="var(--gold)"/>
    <path d="M228 0 H560 V102 L350 152 Q320 158 304 140 Q268 98 242 28 Q236 12 228 0 Z"
          fill="var(--teal)"/>
    <path d="M560 120 V320 H344 L336 210 Q334 180 362 172 Z" fill="var(--gold)"/>
    <path d="M560 127 V320 H350 L342 210 Q341 186 365 179 Z" fill="var(--teal)"/>
  </svg>

  <div class="front-brand"><span class="dot"></span><span>QVR</span></div>

  <div class="holder">
    <p class="holder-name">ADRIAN KELLER</p>
    <p class="holder-role">Managing Director</p>
  </div>

  <ul class="contacts">
    <li>
      <svg viewBox="0 0 12 12"><path d="M2 1 L4.5 1 L5.5 3.5 L4 4.5 Q5 7 7.5 8 L8.5 6.5 L11 7.5 V10 Q11 11 10 11 Q1 10 1 2 Q1 1 2 1 Z" fill="var(--white)"/></svg>
      <span>555-014-2273</span>
    </li>
    <li>
      <svg viewBox="0 0 12 12"><rect x="1" y="2.5" width="10" height="7" rx="1" fill="var(--white)"/><path d="M1.5 3 L6 6.5 L10.5 3" stroke="var(--teal)" stroke-width="1" fill="none"/></svg>
      <span>akeller@quorvane.studio</span>
    </li>
    <li>
      <svg viewBox="0 0 12 12"><circle cx="6" cy="6" r="5" fill="none" stroke="var(--white)" stroke-width="1.2"/><ellipse cx="6" cy="6" rx="2" ry="5" fill="none" stroke="var(--white)" stroke-width="1"/><path d="M1 6 H11" stroke="var(--white)" stroke-width="1"/></svg>
      <span>www.quorvane.studio</span>
    </li>
  </ul>
</section>

</body>
</html>
```